Web Design for an Innovative Life Science Marketplace

IMPORTANT:
The software is called CS-Cart. It has capabilities and limitations with design features in the software. There is a certain framework that needs to be followed. It is PHP and Linux. It may require add-ons for your design, so please be specific with what is required. It’s preferred the designer has CS-Cart knowledge/experience.

Key Requirements
1. I’d like the design to include an implemented/recommended CS-Cart theme that is consistent with our branding (see the marketing collateral and logo).
2. I then need the additional design changes to that theme to create the below web pages.
3. All designs should be consistent with our branding. All pictures should either be computer generated (clip art-like) or pictures of happy patients. What is a happy patient? Close up photo of someone healthy, happy, and experiencing/enjoying life. Not someone in a hospital or getting care. Please see examples already on the site.

Please see the attached Web Design details in the word document. That document is important to complete the design.

```html
<!DOCTYPE html>
<html lang="en">
<head>
<meta charset="utf-8">
<title>CircuLink-QC — Life Science Marketplace</title>
<link rel="stylesheet" href="https://fonts.googleapis.com/css2?family=Roboto:wght@400;500;700;900&family=Roboto+Condensed:wght@400;700&display=swap">
<style>
:root{
  --teal:#169a8a;
  --teal-dark:#0f7f72;
  --green:#8cc63f;
  --green-dark:#79b12c;
  --ink:#3a3a3a;
  --muted:#666;
  --icon:#505050;
  --panel:#f4f4f4;
  --footer:#2b2b2b;
  --white:#fff;
}
*{box-sizing:border-box;margin:0;padding:0}
html,body{width:1200px;height:2539px;overflow:hidden}
body{font-family:"Roboto",Arial,sans-serif;color:var(--ink);background:var(--white);position:relative}

/* top bar */
.topbar{position:absolute;left:0;top:0;width:1200px;height:27px;border-bottom:1px solid #e6e6e6;font-size:10px;color:#555;text-transform:uppercase}
.topbar .item{position:absolute;top:8px;display:flex;align-items:center;gap:6px}
.topbar .ico{width:10px;height:10px;background:var(--teal);border-radius:2px}
.pill{position:absolute;top:3px;height:22px;border-radius:11px;color:#fff;font-size:10px;font-weight:700;display:flex;align-items:center;justify-content:center}

/* header */
.header{position:absolute;left:0;top:27px;width:1200px;height:78px}
.brand{position:absolute;left:162px;top:22px;display:flex;align-items:center;gap:8px;font-weight:900;font-size:24px;color:var(--teal-dark)}
.brand .dot{width:30px;height:30px;border-radius:50%;border:3px solid var(--green)}
.cart{position:absolute;left:633px;top:17px;display:flex;gap:8px}
.cart .box{width:52px;height:44px;background:var(--green);display:flex;align-items:center;justify-content:center}
.cart .title{font-size:14px;color:#555;font-family:"Roboto Condensed",sans-serif}
.cart .count{font-size:20px;color:var(--green);font-weight:700}
.cart .count small{font-size:9px;color:#666;font-weight:400}
.search{position:absolute;left:841px;top:22px;width:192px;height:34px;border-radius:17px;background:#f2f2f2;font-size:10px;color:#999;padding:12px 16px}
.search .go{position:absolute;right:4px;top:5px;width:24px;height:24px;border-radius:50%;background:var(--green)}

/* nav */
.nav{position:absolute;left:0;top:105px;width:1200px;height:41px;background:var(--teal);display:flex;padding-left:160px;font-size:11px;font-weight:500;color:#fff;text-transform:uppercase}
.nav a{display:flex;align-items:center;height:41px;padding:0 24px;color:#fff;text-decoration:none;border-right:1px solid rgba(255,255,255,.18)}
.nav a:first-child{padding-left:2px}

.photo{position:absolute}
.hero{left:0;top:146px;width:1200px;height:232px;background:linear-gradient(90deg,#9ea39c 0%,#c6b49a 35%,#c08a6f 55%,#8e5a45 80%,#6d4538 100%)}

/* section titles */
.heading{position:absolute;left:0;width:1200px;text-align:center;font-weight:700;text-transform:uppercase;color:#555}
.heading .cap{font-size:78px;font-weight:900;color:var(--green);line-height:.8}
.heading .rule{display:inline-block;width:75px;height:2px;background:#555;vertical-align:middle;margin:0 10px}
.heading .teal{color:var(--teal)}

/* join panel */
.join{position:absolute;left:0;top:542px;width:728px;height:311px;background:linear-gradient(90deg,#20a596,#128c7e)}
.join h3{position:absolute;left:160px;top:26px;color:#fff;font-size:22px;font-weight:700;text-transform:uppercase;display:flex;align-items:flex-end}
.join h3 .cap{font-size:72px;font-weight:900;line-height:.8}
.join h3 .rule{display:inline-block;width:46px;height:2px;background:#fff;margin:0 0 11px 8px}
.join h3 .lead{width:18px;height:2px;background:#fff;margin:0 4px 11px 0}
.join ul{position:absolute;list-style:none;color:#fff;font-size:11px;font-weight:500;text-transform:uppercase}
.join li{height:33px;display:flex;gap:6px}
.join li::before{content:"";width:10px;height:10px;border-radius:50%;background:#fff;flex:none;margin-top:1px}
.side-photo{left:735px;top:542px;width:465px;height:311px;background:radial-gradient(circle at 60% 50%,#e7eed3 0%,#b6d27a 40%,#73ad3b 80%)}

/* features */
.feature{position:absolute;text-align:center;font-size:12px;line-height:18px;color:#444}
.feature .badge{width:82px;height:82px;border-radius:50%;background:var(--icon);margin:0 auto 12px;display:flex;align-items:center;justify-content:center}
.feature h4{font-size:16px;font-weight:700;text-transform:uppercase;color:#333;margin-bottom:8px}

.started{position:absolute;left:163px;top:1615px;width:875px;height:156px;background:var(--panel);font-size:11.5px;line-height:19px;color:#666}
.started p{position:absolute;top:44px;width:400px}
.started .divider{position:absolute;left:437px;top:18px;width:1px;height:120px;background:#ddd}

/* contact band */
.contact{position:absolute;left:0;top:1859px;width:1200px;height:147px;background:linear-gradient(90deg,#8cc63f,#9ccf4e 50%,#88c23a)}
.contact .c{position:absolute;top:40px;display:flex;gap:14px;color:#fff}
.contact .ring{width:70px;height:70px;border:3px solid #fff;border-radius:50%;display:flex;align-items:center;justify-content:center}
.contact strong{display:block;font-size:17px;font-weight:500;margin-top:10px}
.contact small{font-size:10px;font-weight:700;text-transform:uppercase}

/* footer */
.footer{position:absolute;left:0;top:2006px;width:1200px;height:486px;background:var(--footer);color:#fff}
.ftitle{position:absolute;font-size:22px;font-weight:700;text-transform:uppercase;display:flex;align-items:flex-end}
.ftitle .cap{font-size:60px;font-weight:900;color:var(--teal);line-height:.8}
.ftitle .under{position:absolute;left:0;bottom:-10px;width:26px;height:2px;background:#fff}
.social{position:absolute;left:538px;top:104px;display:flex;gap:8px}
.social span{width:34px;height:34px;border:1.5px solid #ccc;border-radius:3px}
.email{position:absolute;left:161px;top:268px;width:244px;height:42px;border-radius:21px;background:#d9d9d9;color:#666;font-size:11px;padding:15px 22px;text-transform:uppercase}
.subscribe{position:absolute;left:167px;top:322px;width:128px;height:32px;border-radius:16px;background:var(--teal);font-size:12px;font-weight:700;display:flex;align-items:center;justify-content:center}
.post{position:absolute;left:464px;width:240px;font-size:12px;line-height:18px;color:#bbb}
.post .handle{color:var(--teal);text-decoration:underline}
.post-rule{position:absolute;left:464px;width:240px;height:1px;background:#444}
.map{left:758px;top:2270px;width:270px;height:152px;background:linear-gradient(135deg,#e8e4d8 0%,#dfe5d0 45%,#a9c3e0 70%,#8fb2da 100%)}

.bottom{position:absolute;left:0;top:2492px;width:1200px;height:47px;background:var(--teal);color:#fff;font-size:10px;text-transform:uppercase}
.bottom nav{position:absolute;left:172px;top:19px;display:flex}
.bottom nav span{margin-right:46px}
.bottom .copy{position:absolute;right:160px;top:19px}
</style>
</head>
<body>

<div class="topbar">
  <div class="item" style="left:161px"><span class="ico"></span>Adress : 48 Harbor Lane, NY</div>
  <div class="item" style="left:398px"><span class="ico"></span>Email : hello@circulink.example</div>
  <div class="item" style="left:616px"><span class="ico"></span>Call us : 555-014-2290</div>
  <div class="item" style="left:790px"><span class="ico" style="background:#666;border-radius:50%"></span>My Account</div>
  <div class="pill" style="left:890px;width:63px;background:var(--teal)">Login</div>
  <div class="pill" style="left:957px;width:80px;background:var(--green)">Register</div>
</div>

<header class="header">
  <div class="brand"><span class="dot"></span>CIRCULINK-QC</div>
  <div class="cart">
    <div class="box"><svg width="30" height="26" viewBox="0 0 30 26" fill="none" stroke="#fff" stroke-width="2.4"><path d="M2 3h5l3 14h15l3-10H9"/><circle cx="12" cy="22" r="2"/><circle cx="23" cy="22" r="2"/></svg></div>
    <div><div class="title">SHOPPING CART</div><div class="count">(0) <small>ITEM SELECTED</small></div></div>
  </div>
  <div class="search">Search Product....<span class="go"></span></div>
</header>

<nav class="nav">
  <a>Home</a><a>About us</a><a>How it works</a><a>Our platform</a><a>Benefits</a><a style="border:0">Contact us</a>
</nav>

<div class="photo hero" role="img" aria-label="Close-up photo of a smiling woman in glasses against a brick wall"></div>

<h2 class="heading" style="top:436px;font-size:28px"><span class="rule" style="width:22px"></span><span class="cap">W</span>hy CircuLink-QC?<span class="rule"></span></h2>

<section class="join">
  <h3><span class="lead"></span><span class="cap">W</span>hy join this circular supply chain?<span class="rule"></span></h3>
  <ul style="left:160px;top:121px">
    <li>Reduce your write-downs</li><li>Reduce your carbon footprint</li><li>Purchase material at lower prices</li>
    <li>Collaborate with the LS community to solve problems</li><li>Transfer benefits back to patients</li>
  </ul>
  <ul style="left:480px;top:121px">
    <li>Reduce your disposal fees</li><li>Donate material</li><li>Avoid stock outs</li>
  </ul>
</section>
<div class="photo side-photo" role="img" aria-label="Photo of a happy woman stretching outdoors among green leaves"></div>

<h2 class="heading" style="top:895px;font-size:28px;line-height:40px">
  <span class="cap">W</span>hy use<br><span class="rule" style="width:26px"></span><span class="teal" style="font-size:34px">CircuLink-QC?</span><span class="rule"></span>
</h2>

<div class="feature" style="left:165px;top:1041px;width:275px">
  <div class="badge"><svg width="44" height="48" viewBox="0 0 44 48" fill="#fff"><circle cx="22" cy="18" r="16"/><path d="M12 30l-5 16 8-4 4 6 3-14zM32 30l5 16-8-4-4 6-3-14z"/><path d="M15 18l5 5 9-9" stroke="#505050" stroke-width="3" fill="none"/></svg></div>
  <h4>Quality Compliance</h4>Part 11 aligned marketplace<br>cGMP emphasis on transactional information<br>We monitor and regulate the marketplace
</div>
<div class="feature" style="left:488px;top:1041px;width:260px">
  <div class="badge"><svg width="34" height="44" viewBox="0 0 34 44"><rect x="1" y="1" width="32" height="42" fill="#fff"/><path d="M8 12h18M8 19h18M8 26h18M8 33h12" stroke="#505050" stroke-width="2.5"/></svg></div>
  <h4>Aligned Marketplace</h4>Our Terms of Quality is signed by all account owners.&nbsp; It outlines baseline responsibilities within the marketplace to ensure transactional alignment.
</div>
<div class="feature" style="left:810px;top:1041px;width:240px">
  <div class="badge"><svg width="48" height="42" viewBox="0 0 48 42" fill="#fff"><circle cx="24" cy="8" r="6"/><circle cx="9" cy="28" r="5"/><circle cx="39" cy="28" r="5"/><path d="M1 42a8 8 0 0116 0zM31 42a8 8 0 0116 0z"/><path d="M24 14v10M24 24L11 24M24 24h13" stroke="#fff" stroke-width="2"/></svg></div>
  <h4>Industry Partners</h4>Our vetted partners and service providers<br>are some of the best in the industry.
</div>
<div class="feature" style="left:235px;top:1253px;width:395px">
  <div class="badge"><svg width="46" height="40" viewBox="0 0 46 40"><path d="M23 38L4 20A11 11 0 0123 6a11 11 0 0119 14z" fill="#fff"/></svg></div>
  <h4>Our Passion</h4>No one can match our passion for patients and consumers of our industry. We want to transform the LS industry paradigm of waste by using our platform as a springboard to create better access for patients, better quality products, and less environmental impact on our communities.
</div>
<div class="feature" style="left:700px;top:1253px;width:240px">
  <div class="badge"><svg width="48" height="44" viewBox="0 0 48 44"><circle cx="28" cy="13" r="11" fill="none" stroke="#fff" stroke-width="2.5"/><text x="28" y="18" font-size="14" font-family="Roboto,sans-serif" fill="#fff" text-anchor="middle">$</text><path d="M2 32h12l10 4h14l8-6v4l-10 8H20L10 40H2z" fill="#fff"/></svg></div>
  <h4>Lost Cost</h4>printing and typesetting industry. Lorem Ipsum has been the industry's standard unknown printer took a galley of type and scrambled it to make a type specimen book.
</div>

<h2 class="heading" style="top:1488px;font-size:28px;line-height:42px">
  <span class="cap">W</span>hy get<br><span class="rule" style="width:26px"></span><span class="teal" style="font-size:34px">Started today</span><span class="rule"></span>
</h2>

<section class="started">
  <p style="left:28px">Governmental and societal pressure on consumer goods and medicine prices continue to mount.&nbsp; Widespread demand to reduce carbon footprints strengthen by the day. Tolerance among our communities is growing thin.</p>
  <span class="divider"></span>
  <p style="left:473px;top:40px;width:380px">All companies need an outlet to optimize waste and protect their supply chains rather than transferring that waste to customers.&nbsp; All suppliers need a marketplace network to leverage.&nbsp; The time is now to change our ways of working as an industry.</p>
</section>

<section class="contact">
  <div class="c" style="left:171px"><span class="ring"><svg width="30" height="30" viewBox="0 0 24 24" fill="#fff"><path d="M6.6 10.8a15 15 0 006.6 6.6l2.2-2.2c.3-.3.7-.4 1-.2 1.1.4 2.3.6 3.6.6.6 0 1 .4 1 1V20c0 .6-.4 1-1 1A17 17 0 013 4c0-.6.4-1 1-1h3.5c.6 0 1 .4 1 1 0 1.3.2 2.5.6 3.6.1.3 0 .7-.2 1z"/></svg></span><div><strong>555-014-2290</strong><small>Call us for enquiry</small></div></div>
  <div class="c" style="left:467px"><span class="ring"><svg width="32" height="24" viewBox="0 0 32 24" fill="none" stroke="#fff" stroke-width="2"><rect x="1" y="1" width="30" height="22"/><path d="M1 1l15 12L31 1M1 23l11-10M31 23L20 13"/></svg></span><div><strong>hello@circulink.example</strong><small>Drop us a line anytime!</small></div></div>
  <div class="c" style="left:795px"><span class="ring"><svg width="24" height="32" viewBox="0 0 24 32" fill="#fff"><path d="M12 0a12 12 0 0112 12c0 9-12 20-12 20S0 21 0 12A12 12 0 0112 0z"/><circle cx="12" cy="12" r="5" fill="#8cc63f"/></svg></span><div><strong>48 Harbor Lane, NY</strong><small>Company address</small></div></div>
</section>

<footer class="footer">
  <div class="ftitle" style="left:484px;top:42px"><span class="cap">C</span>onnect with us</div>
  <div class="social" aria-label="Social links"><span></span><span></span><span></span></div>

  <div class="ftitle" style="left:160px;top:200px"><span class="cap">N</span>ewsletter<span class="under"></span></div>
  <div class="email">Enter your email id</div>
  <div class="subscribe">SUBSCRIBE</div>

  <div class="ftitle" style="left:464px;top:200px"><span class="cap">U</span>pdates<span class="under"></span></div>
  <p class="post" style="top:268px"><span class="handle">@circu_lk:</span> Phasellus dapibus tellus at nibh lobortis, vitae placerat sapien tempor.</p>
  <span class="post-rule" style="top:308px"></span>
  <p class="post" style="top:320px"><span class="handle">@circu_lk:</span> Phasellus dapibus tellus at nibh lobortis, vitae placerat sapien tempor.</p>
  <span class="post-rule" style="top:360px"></span>
  <p class="post" style="top:376px"><span class="handle">@circu_lk:</span> Phasellus dapibus tellus at nibh lobortis, vitae placerat sapien tempor.</p>

  <div class="ftitle" style="left:756px;top:200px"><span class="cap">L</span>ocation<span class="under"></span></div>
</footer>
<div class="photo map" role="img" aria-label="Street map showing the company location by the waterfront"></div>

<div class="bottom">
  <nav><span>Home</span><span>About us</span><span>How it works</span><span>Our platform</span><span>Benefits</span><span>Contact us</span></nav>
  <div class="copy">© 2018 CircuLink . All rights reserved</div>
</div>

</body>
</html>
```